Threat Lens ratings for Apps and Games

I need a web site designing that is aimed at parents and will show an "Threat Lens" rating for apps and games. I have attached a document with an overview of what the Threat Lens is. The website needs to be easy for parents to navigate and find what they want quickly and easily. I should also be able to update the website myself easily with "reviews" of the attack vectors for apps and games.

Target Market(s)

Parents

Coding

Coded - Design and coding required

Number of Pages Required

2 page

Requirements
Must have
• Clear and concise ratings for apps and games

```html
<!DOCTYPE html>
<html lang="en">
<head>
<meta charset="utf-8">
<title>Threat Lens – Ratings for Apps and Games</title>
<link href="https://fonts.googleapis.com/css2?family=Lato:ital,wght@0,400;0,700;0,900;1,400&display=swap" rel="stylesheet">
<style>
:root{
  --orange:#f7890c;
  --green:#4cb825;
  --blue:#1a64b8;
  --ink:#222222;
  --text:#333333;
  --muted:#555555;
  --band:#f0f0f0;
  --white:#ffffff;
  --footer:#1c1c1c;
  --hero-a:#6f7177;
  --hero-b:#3d4046;
}
*{box-sizing:border-box;margin:0;padding:0}
html,body{width:1200px;height:3231px;overflow:hidden}
body{position:relative;font-family:'Lato',sans-serif;color:var(--text);background:var(--white)}
a{color:inherit;text-decoration:none}
.abs{position:absolute}

/* hero */
.hero-bg{left:0;top:0;width:1200px;height:784px;
  background:linear-gradient(110deg,var(--hero-a) 0%,#5d6066 45%,var(--hero-b) 70%,#2b3550 100%);
  clip-path:polygon(0 0,1200px 0,1200px 784px,0 677px)}
.brand{left:76px;top:52px;font-size:40px;font-weight:700;color:var(--white);letter-spacing:.3px}
.nav{top:66px;left:459px;display:flex;gap:44px;font-size:18px;font-weight:700;color:var(--white)}
.btn{display:flex;align-items:center;justify-content:center;border-radius:26px;font-weight:700;color:var(--white);font-size:19px}
.btn-login{left:1008px;top:58px;width:118px;height:42px;background:var(--green)}
.hero-title{left:76px;top:244px;font-size:55px;line-height:60px;font-weight:700;color:var(--white)}
.hero-sub{left:76px;top:370px;width:600px;font-size:20px;line-height:30px;font-weight:700;color:#f2f2f2}
.btn-orange{background:var(--orange)}
.hero-cta{left:76px;top:453px;width:175px;height:51px}

/* about */
.about-photo{left:0;top:849px;width:524px;height:355px;border-radius:0 10px 10px 0;
  background:linear-gradient(135deg,#d9d4cc,#c7bba8 45%,#8aa0c2 100%)}
.h2{font-size:55px;line-height:55px;font-weight:900;color:var(--ink)}
.about-title{left:558px;top:860px}
.about-text{left:558px;top:984px;width:560px;font-size:18.5px;line-height:31.3px;color:var(--text)}
.about-cta{left:558px;top:1137px;width:175px;height:52px}

/* features */
.features-bg{left:0;top:1252px;width:1200px;height:688px;background:var(--band);
  clip-path:polygon(0 0,1200px 102px,1200px 688px,0 688px)}
.features-title{left:74px;top:1394px}
.feature{position:absolute;width:340px;height:80px}
.feature .ic{position:absolute;left:0;top:0;width:74px;height:74px;border:2px solid var(--orange);border-radius:50%;
  display:flex;align-items:center;justify-content:center;background:var(--white)}
.feature h3{position:absolute;left:89px;top:-5px;font-size:17.5px;font-weight:700;color:var(--blue)}
.feature p{position:absolute;left:89px;top:21px;width:260px;font-size:15px;line-height:25px;color:var(--muted)}
.features-cta{left:76px;top:1820px;width:175px;height:51px}
.phone-art{left:820px;top:1300px;width:290px;height:580px;border-radius:44px;transform:rotate(6deg);
  background:linear-gradient(180deg,#bfe0ee,#a6d2e6);border:7px solid #1a1a1a}

/* testimonials */
.testi-title{left:75px;top:2000px;font-size:56px}
.arrows{left:1072px;top:2014px}
.testi{position:absolute;top:2098px;width:340px}
.stars{display:flex;gap:9px;margin-bottom:14px}
.testi p{font-style:italic;font-size:16.5px;line-height:30.5px;color:var(--text);white-space:nowrap}
.testi h4{margin-top:12px;font-size:17px;font-weight:700;color:var(--ink)}

/* subscribe */
.sub-bg{left:0;top:2374px;width:1200px;height:439px;background:var(--band);
  clip-path:polygon(0 0,1200px 0,1200px 335px,0 439px)}
.sub-title{left:0;top:2438px;width:1200px;text-align:center;font-size:56px}
.sub-text{left:0;top:2522px;width:1200px;text-align:center;font-size:19px;color:var(--text)}
.email{left:278px;top:2584px;width:464px;height:51px;border:1px solid #bdbdbd;border-radius:26px;background:var(--white);
  font-size:14px;color:#333;display:flex;align-items:center;padding-left:27px}
.sub-btn{left:751px;top:2584px;width:174px;height:51px}

/* footer */
.fcol{position:absolute;top:2858px}
.fcol h5{font-size:34px;font-weight:700;color:var(--ink);margin-bottom:16px}
.fcol p{font-size:15px;line-height:27.6px;color:var(--text);white-space:nowrap}
.fcol ul{list-style:none;font-size:15px;color:var(--text)}
.fcol li{height:34px;line-height:34px}
.fcol.wide li{height:40.5px;line-height:40.5px}
.bottom{left:0;top:3150px;width:1200px;height:81px;background:var(--footer)}
.copy{left:75px;top:3184px;font-size:15.5px;color:#e6e6e6}
.social{left:954px;top:3184px;display:flex;gap:22px}
.social span{width:18px;height:18px;border-radius:50%;background:#e6e6e6;display:block}
</style>
</head>
<body>

<!-- Hero -->
<div class="abs hero-bg" role="img" aria-label="Photo of a young boy on a sofa looking at a smartphone"></div>
<div class="abs brand">Threat Lens</div>
<nav class="abs nav"><a href="#">Home</a><a href="#">About Us</a><a href="#">Features</a><a href="#">Reviews</a><a href="#">Blog</a></nav>
<a class="abs btn btn-login" href="#">Log In</a>
<h1 class="abs hero-title">Threat Lens Ratings for<br>Apps and Games</h1>
<p class="abs hero-sub">Sed ut perspiciatis unde omnis iste natus error sit voluptatem accusantium doloremque.</p>
<a class="abs btn btn-orange hero-cta" href="#">Try it’s Free</a>

<!-- About -->
<div class="abs about-photo" role="img" aria-label="Photo of a mother and daughter smiling at a phone on a sofa"></div>
<h2 class="abs h2 about-title">About<br>Threat Lens</h2>
<p class="abs about-text">To be very clear - now a days children using phone they may even<br>get some popup without knowing if they accept it - may phone<br>&nbsp;get hacked so on this case parents will wasth their child by using<br>threat lens.</p>
<a class="abs btn btn-orange about-cta" href="#">Read More</a>

<!-- Features -->
<div class="abs features-bg"></div>
<h2 class="abs h2 features-title">Features</h2>

<div class="feature" style="left:75px;top:1484px">
  <div class="ic"><svg width="28" height="28" viewBox="0 0 24 24"><path d="M3 21l1-5L16 4l4 4L8 20z" fill="#1d1d1d"/><path d="M14 6l4 4" stroke="#fff" stroke-width="1.5"/></svg></div>
  <h3>Login</h3><p>Sed ut perspiciatis unde omnis iste natus error sit voluptate</p>
</div>
<div class="feature" style="left:434px;top:1484px">
  <div class="ic"><svg width="24" height="28" viewBox="0 0 24 28"><path d="M12 27s9-10 9-17a9 9 0 10-18 0c0 7 9 17 9 17z" fill="#1d1d1d"/><circle cx="12" cy="10" r="3.5" fill="#fff"/></svg></div>
  <h3>Location Services</h3><p>Sed ut perspiciatis unde omnis iste natus error sit voluptate</p>
</div>
<div class="feature" style="left:75px;top:1590px">
  <div class="ic"><svg width="32" height="28" viewBox="0 0 32 28"><ellipse cx="13" cy="11" rx="12" ry="9" fill="#1d1d1d"/><ellipse cx="21" cy="17" rx="10" ry="8" fill="#1d1d1d" stroke="#fff" stroke-width="1.5"/><path d="M27 22l3 5-7-3z" fill="#1d1d1d"/></svg></div>
  <h3>Chat/Messaging</h3><p>Sed ut perspiciatis unde omnis iste natus error sit voluptate</p>
</div>
<div class="feature" style="left:434px;top:1590px">
  <div class="ic"><svg width="32" height="22" viewBox="0 0 32 22"><rect x="0" y="1" width="21" height="20" rx="3" fill="#1d1d1d"/><path d="M22 8l10-6v18l-10-6z" fill="#1d1d1d"/></svg></div>
  <h3>Live Streaming</h3><p>Sed ut perspiciatis unde omnis iste natus error sit voluptate</p>
</div>
<div class="feature" style="left:75px;top:1696px">
  <div class="ic"><svg width="28" height="24" viewBox="0 0 28 24"><path d="M2 6h6l2-4h8l2 4h6v17H2z" fill="#1d1d1d"/><circle cx="14" cy="14" r="5.5" fill="#fff"/><circle cx="14" cy="14" r="3.5" fill="#1d1d1d"/></svg></div>
  <h3>Camera/Microphone Access</h3><p>Sed ut perspiciatis unde omnis iste natus error sit voluptate</p>
</div>

<a class="abs btn btn-orange features-cta" href="#">Read More</a>
<div class="abs phone-art" role="img" aria-label="Illustration of a smartphone showing a cartoon boy walking while using a phone"></div>

<!-- Testimonials -->
<h2 class="abs h2 testi-title">Testimonials</h2>
<svg class="abs arrows" width="56" height="30" viewBox="0 0 56 30" aria-label="Previous and next"><path d="M16 5L6 15l10 10" fill="none" stroke="#222" stroke-width="2.2"/><path d="M40 5l10 10-10 10" fill="none" stroke="#222" stroke-width="2.2"/></svg>

<svg width="0" height="0" style="position:absolute"><defs><path id="star" d="M10 1l2.8 5.8 6.2.9-4.5 4.4 1.1 6.3L10 15.4 4.4 18.4l1.1-6.3L1 7.7l6.2-.9z" fill="#f7890c"/></defs></svg>

<div class="testi" style="left:75px">
  <div class="stars"><svg width="20" height="20"><use href="#star"/></svg><svg width="20" height="20"><use href="#star"/></svg><svg width="20" height="20"><use href="#star"/></svg><svg width="20" height="20"><use href="#star"/></svg><svg width="20" height="20"><use href="#star"/></svg></div>
  <p>Sed ut perspiciatis unde omnis iste natus<br>error sit voluptate ab illo inventore veritatis et<br>quasi architecto beatae vitae dicta sunt<br>explicabo..</p>
  <h4>Name Heading</h4>
</div>
<div class="testi" style="left:435px">
  <div class="stars"><svg width="20" height="20"><use href="#star"/></svg><svg width="20" height="20"><use href="#star"/></svg><svg width="20" height="20"><use href="#star"/></svg><svg width="20" height="20"><use href="#star"/></svg><svg width="20" height="20"><use href="#star"/></svg></div>
  <p>Sed ut perspiciatis unde omnis iste natus<br>error sit voluptate ab illo inventore veritatis et<br>quasi architecto beatae vitae dicta sunt<br>explicabo..</p>
  <h4>Name Heading</h4>
</div>
<div class="testi" style="left:798px">
  <div class="stars"><svg width="20" height="20"><use href="#star"/></svg><svg width="20" height="20"><use href="#star"/></svg><svg width="20" height="20"><use href="#star"/></svg><svg width="20" height="20"><use href="#star"/></svg><svg width="20" height="20"><use href="#star"/></svg></div>
  <p>Sed ut perspiciatis unde omnis iste natus<br>error sit voluptate ab illo inventore veritatis et<br>quasi architecto beatae vitae dicta sunt<br>explicabo..</p>
  <h4>Name Heading</h4>
</div>

<!-- Subscribe -->
<div class="abs sub-bg"></div>
<h2 class="abs h2 sub-title">Subscribe Email</h2>
<p class="abs sub-text">Sed ut perspiciatis unde omnis iste natus error sit voluptatem accusantium doloremque laudantium,</p>
<div class="abs email">Enter Email Address</div>
<a class="abs btn btn-orange sub-btn" href="#">Subscribe</a>

<!-- Footer -->
<div class="fcol" style="left:75px;width:260px">
  <h5>Company</h5>
  <p>Sed ut perspiciatis unde omnis iste<br>natus error sit voluptatem<br>accusantium doloremque &nbsp;dantium,<br>totam rem aperiam, eaque ipsa<br>quae ab illo inventore</p>
</div>
<div class="fcol" style="left:396px">
  <h5>Features</h5>
  <ul><li>Login</li><li>Chat/Messaging</li><li>Camera/Microphone Access</li><li>Location Services</li><li>Live Streaming</li></ul>
</div>
<div class="fcol wide" style="left:654px">
  <h5>Support</h5>
  <ul><li>Sed ut perspiciatis</li><li>Unde omnis iste</li><li>Natus error sit voluptatem</li><li>Accusantium</li></ul>
</div>
<div class="fcol wide" style="left:911px">
  <h5>Legal</h5>
  <ul><li>Sed ut perspiciatis</li><li>Unde omnis iste</li><li>Natus error sit voluptatem</li><li>Accusantium</li></ul>
</div>

<div class="abs bottom"></div>
<p class="abs copy">Copyright © 2021 Company Name. All Right Reserved</p>
<div class="abs social" aria-label="Social links"><span></span><span></span><span></span><span></span><span></span></div>

</body>
</html>
```